New Coffee Shop business card

We are opening our new coffee shop and are needing business cards to take with us on February 6th to Atlanta, Ga to a show.

We will be offering the following menu type items:

coffee
teas
espresso
frappes
smoothies

sandwiches
soups
salads
pastries
ice cream

Our shop is in a rural country-side area and we would like to convey that feel in our shop. In addition to the cafe we will also be selling gifts and furniture and other home decor. Much of this merchandise will be rescued, refurbished or repurposed which is also a core value of what we are all about.

We have a company logo we would like incorporated into the design.

We will also provide files that have the elements of the logo which may also be useful in the design of the card.

Since we are not open yet we need one slightly altered version of the card as well as the final product which states "Opening in the summer 2015"

Target Market(s)

moderate to slightly upscale and folksy.

Industry/Entity Type

Coffee Shop

Contact Information for Business Card

Fern Kettle Coffee
name
address
phone number
email

Card

Font styles to use
Sans Serif

Requirements
Must have
• Must include Logo
• Must include information on menu.
• Must include information on our merchandise sales as described inthe project description.
• Color scheme to complement the logo
Nice to have
• The following descriptions
• "We are also selling gifts, furniture, and other home decoration."
• "We rescue, refurbish, and repurpose old furniture so it can live again."

```html
<!DOCTYPE html>
<html lang="en">
<head>
<meta charset="utf-8">
<title>Fern Kettle Coffee – Business Cards</title>
<link href="https://fonts.googleapis.com/css2?family=Jost:wght@400&family=Handlee&display=swap" rel="stylesheet">
<style>
  :root {
    --bg: #e9e4dc;
    --red-light: #c23f53;
    --red-dark: #8f2337;
    --black: #151515;
    --black-soft: #2a2a2a;
    --white: #ffffff;
    --pink-text: #f3d5da;
    --ornament: #efe9ea;
    --shadow: rgba(0,0,0,0.25);
  }
  * { margin: 0; padding: 0; box-sizing: border-box; }
  html, body { width: 1200px; height: 1000px; overflow: hidden; }
  body {
    background: var(--bg);
    font-family: "Jost", sans-serif;
    color: var(--white);
    position: relative;
  }
  .card {
    position: absolute;
    left: 220px;
    width: 760px;
    height: 434px;
    display: flex;
    overflow: hidden;
    border-radius: 3px;
    box-shadow: 0 10px 24px var(--shadow);
  }
  .card--front { top: 46px; }
  .card--back { top: 520px; }

  .panel-red {
    background: linear-gradient(135deg, var(--red-light) 0%, var(--red-dark) 100%);
    position: relative;
  }
  .panel-black {
    background: linear-gradient(160deg, var(--black-soft) 0%, var(--black) 60%);
    position: relative;
  }

  /* front */
  .card--front .panel-black { width: 224px; }
  .card--front .panel-red { flex: 1; }
  .brand {
    position: absolute;
    left: 0; right: 0; top: 0; bottom: 0;
    display: flex; align-items: center; justify-content: center;
    gap: 12px;
  }
  .brand__mark { width: 18px; height: 18px; background: var(--white); }
  .brand__name {
    font-size: 30px; line-height: 1.05; color: var(--white); font-weight: 400;
  }
  .tagline {
    position: absolute; left: 30px; top: 34px;
    font-size: 24px; letter-spacing: 0.5px;
  }
  .owner-name {
    position: absolute; left: 30px; top: 78px;
    font-family: "Handlee", cursive; font-size: 36px; line-height: 1.1;
    width: 330px;
  }
  .owner-rule {
    position: absolute; left: 30px; top: 170px;
    width: 320px; height: 2px; background: var(--white);
  }
  .owner-role {
    position: absolute; left: 356px; top: 120px;
    font-size: 15px; color: var(--pink-text);
  }
  .cup-art {
    position: absolute; right: 24px; top: 22px;
    width: 120px; height: 120px;
  }
  .contact {
    position: absolute; left: 30px; top: 206px;
    list-style: none; font-size: 18px; line-height: 1;
    color: var(--pink-text);
  }
  .contact li { margin-bottom: 26px; }

  /* back */
  .card--back .panel-red { width: 470px; }
  .card--back .panel-black { flex: 1; }
  .menu-title {
    position: absolute; left: 170px; top: 28px;
    font-size: 40px; line-height: 1;
  }
  .menu-sub {
    position: absolute; left: 172px; top: 74px;
    font-size: 22px; color: var(--pink-text);
  }
  .ornament { position: absolute; }
  .ornament--title { left: 40px; top: 30px; width: 110px; height: 70px; }
  .ornament--mid { left: 170px; top: 130px; width: 120px; height: 60px; }
  .ornament--side { left: 40px; top: 112px; width: 180px; height: 70px; }
  .menu-list {
    position: absolute; list-style: none;
    font-size: 20px; line-height: 1.3; color: var(--pink-text);
  }
  .menu-list--drinks { left: 40px; top: 230px; }
  .menu-list--food { left: 250px; top: 230px; }
  .more-title {
    position: absolute; left: 30px; top: 26px;
    font-size: 34px; line-height: 1.1;
  }
  .more-text {
    position: absolute; left: 30px; top: 200px; width: 240px;
    font-size: 16px; line-height: 1.45;
  }
</style>
</head>
<body>

<section class="card card--front" aria-label="Business card front">
  <div class="panel-black">
    <div class="brand">
      <span class="brand__mark"></span>
      <span class="brand__name">Fern Kettle<br>Coffee</span>
    </div>
  </div>
  <div class="panel-red">
    <p class="tagline">The Head Kettlers</p>
    <p class="owner-name">Dale and Mabel Harlow</p>
    <div class="owner-rule"></div>
    <p class="owner-role">owners</p>
    <svg class="cup-art" viewBox="0 0 120 120" role="img" aria-label="Coffee cup with curling steam flourish">
      <rect x="0" y="0" width="120" height="120" rx="6" fill="var(--ornament)" opacity="0.35"/>
    </svg>
    <ul class="contact">
      <li>Address:</li>
      <li>phone: 555 014 2290</li>
      <li>email: hello@fernkettle.example</li>
      <li>Card:</li>
    </ul>
  </div>
</section>

<section class="card card--back" aria-label="Business card back">
  <div class="panel-red">
    <svg class="ornament ornament--title" viewBox="0 0 110 70" role="img" aria-label="Decorative swirl flourish">
      <rect width="110" height="70" rx="6" fill="var(--ornament)" opacity="0.35"/>
    </svg>
    <h2 class="menu-title">coffee shop</h2>
    <p class="menu-sub">stuff we’re selling...</p>
    <svg class="ornament ornament--mid" viewBox="0 0 120 60" role="img" aria-label="Decorative swirl flourish">
      <rect width="120" height="60" rx="6" fill="var(--ornament)" opacity="0.35"/>
    </svg>
    <ul class="menu-list menu-list--drinks">
      <li>coffee</li><li>teas</li><li>espresso</li><li>frappes</li><li>smoothies</li>
    </ul>
    <ul class="menu-list menu-list--food">
      <li>sandwiches</li><li>soups</li><li>salads</li><li>pastries</li><li>ice cream</li>
    </ul>
  </div>
  <div class="panel-black">
    <h2 class="more-title">Not just a<br>coffee shop....</h2>
    <svg class="ornament ornament--side" viewBox="0 0 180 70" role="img" aria-label="Decorative swirl flourish">
      <rect width="180" height="70" rx="6" fill="var(--ornament)" opacity="0.3"/>
    </svg>
    <p class="more-text">An eclectic assemblage of gifts, furnishings, and home decor. We rescue, refurbish, and repurpose old furniture so it can live again.</p>
  </div>
</section>

</body>
</html>
```